Scrum Master & Agile IT Coach Needing Business Website

Hello, my name is Joel Brandt
I am a project manger, scrum master, & agile coach. I work with IT development teams on major projects for Summit 300 companies . My project management business has a website and can be found here: www.tk-steadfast.example

I have launched a new company, ALL focused on IT Agile Coaching, I am looking to have a website created for my new company - the name of the new company is: Q's and V's - Agile IT Coaching and Training.
I have a logo and it is provided in the materials. I like to logo; I am open to different color pallets.

The website will have a total of 7 pages; I have content for 5 of the 7 pages prepared; the other 2 pages will say under construction.

Page 1 Who am I, What I do, My Experience
Demonstrated experience and progression from Scrum Master to
Program Manager to Coach

Page 2 Q's & V's - Agile Team Coaching
teams working major IT projects, multiple months/years

Page 3 Coaching @ the Team Level

Page 4 Coaching @ the Program Level ; LIMBr ART level

Pages 5 -6 Under Construction

Page 7 Presentations, Slide Decks, Reference Materials

Mentors Nook need to have this highlighted somewhere Monthly Blog
Updates

Industry/Entity Type

IT development

Coding

Coded - Design and coding required

Number of Pages Required

5+ page

Requirements
Must have
• the website must be bold - I want those who visit to remember coming to my coaching site
Nice to have
• nice to have will be a modern / futuristic website; I work with IT developers, I want a website they will like
Should not have
• should not be stiff - it should be professional but fun

```html
<!DOCTYPE html>
<html lang="en">
<head>
<meta charset="utf-8">
<title>Q's and V's – Joel Brandt</title>
<link href="https://fonts.googleapis.com/css2?family=Poppins:wght@400;500;600;700&display=swap" rel="stylesheet">
<style>
:root{
  --blue:#0a9be0;
  --blue-deep:#13508f;
  --blue-mid:#0679b4;
  --navy:#124a8c;
  --ink:#111;
  --text:#333;
  --exp-bg:#eaf0f3;
  --white:#fff;
}
*{box-sizing:border-box;margin:0;padding:0}
html,body{width:1200px;height:2844px;overflow:hidden}
body{font-family:'Poppins',sans-serif;color:var(--text);position:relative;background:var(--white)}
a{color:inherit;text-decoration:none}

.site-header{position:absolute;top:0;left:0;width:1200px;height:100px;z-index:3;display:flex;align-items:center;justify-content:space-between;padding:0 105px 0 72px}
.brand{font-weight:400;font-size:22px;color:var(--text)}
.main-nav{display:flex;gap:39px;font-size:15px;color:#333}

.hero{position:absolute;top:0;left:0;width:1200px;height:600px;background:linear-gradient(135deg,#f3f4f6 0%,#e8eaee 100%);overflow:hidden}
.hero-intro{position:absolute;left:100px;top:232px}
.hero-kicker{font-size:22px;color:#333}
.hero-name{font-size:40px;font-weight:700;color:var(--blue);margin-top:8px;line-height:1.2}
.hero-role{font-size:16.5px;color:#222;width:330px;line-height:26px;margin-top:14px}
.btn-solid{display:inline-block;background:linear-gradient(180deg,#0a72b5,#13508f);color:var(--white);font-weight:600;font-size:15px;border-radius:3px}
.hero .btn-solid{margin-top:20px;padding:10px 14px}
.hero-portrait{position:absolute;left:675px;top:120px;width:303px;height:480px;border-radius:151px 151px 0 0;background:linear-gradient(180deg,#1596d8,#0b74b8)}

.designations{position:absolute;top:600px;left:0;width:1200px;height:490px;background:linear-gradient(180deg,var(--blue-mid) 0%,var(--blue-deep) 100%);text-align:center}
.section-title-light{color:var(--white);font-size:30px;font-weight:700;margin-top:76px}
.badge-row{position:absolute;top:159px;left:0;width:1200px}
.badge{position:absolute;width:133px;height:133px;border-radius:50%;background:var(--white);box-shadow:0 4px 10px rgba(0,0,0,.2);display:flex;align-items:center;justify-content:center}
.badge span{width:88px;height:88px;border-radius:50%;display:block}
.profile-links{position:absolute;top:343px;left:0;width:1200px}
.profile-link{position:absolute;height:42px;background:var(--white);color:var(--blue);font-weight:600;font-size:14.5px;display:flex;align-items:center;justify-content:center;border-radius:2px}

.services{position:absolute;top:1090px;left:0;width:1200px;height:545px;background:var(--white)}
.section-title{color:var(--ink);font-size:30px;font-weight:700;text-align:center}
.services .section-title{margin-top:68px}
.service{position:absolute;top:175px;width:180px;text-align:center}
.service-card{width:180px;height:217px;background:var(--white);border-radius:8px;box-shadow:0 2px 12px rgba(0,0,0,.12);display:flex;align-items:center;justify-content:center}
.service-name{font-size:17px;color:#222;line-height:27px;margin-top:22px;width:260px;margin-left:-40px}

.experience{position:absolute;top:1635px;left:0;width:1200px;height:863px;background:var(--exp-bg)}
.experience .section-title{margin-top:89px}
.exp-grid{position:absolute;left:103px;top:172px;width:993px;height:486px;display:grid;grid-template-columns:331px 331px 331px;grid-template-rows:243px 243px;box-shadow:0 4px 14px rgba(0,0,0,.08)}
.exp-photo{width:100%;height:100%}
.exp-text{background:var(--white);text-align:center;padding:28px 22px 0}
.exp-text h3{color:var(--blue);font-size:18px;font-weight:600;line-height:24px}
.exp-text p{font-size:11.8px;line-height:21px;color:#444;margin-top:18px}
.experience .btn-solid{position:absolute;left:431px;top:725px;width:338px;height:42px;display:flex;align-items:center;justify-content:center;font-size:14px;text-transform:uppercase}

.site-footer{position:absolute;top:2498px;left:0;width:1200px;height:346px;background:var(--navy);color:var(--white);text-align:center}
.site-footer .brand{color:var(--white);font-size:32px;position:absolute;top:82px;left:0;width:1200px}
.subscribe{position:absolute;left:362px;top:167px;width:475px;height:38px;border:2px solid var(--white);display:flex;align-items:center;padding:3px}
.subscribe-field{flex:1;text-align:left;font-size:15px;padding-left:7px;color:#dfe6f1}
.subscribe-btn{background:var(--white);color:var(--navy);font-weight:600;font-size:14px;width:92px;height:28px;display:flex;align-items:center;justify-content:center}
.footer-nav{position:absolute;top:233px;left:0;width:1200px;display:flex;justify-content:center;gap:22px;font-size:15.5px}
.copyright{position:absolute;top:294px;left:0;width:1200px;font-size:14px}
</style>
</head>
<body>

<section class="hero">
  <div class="hero-intro">
    <p class="hero-kicker">- Who am I</p>
    <h1 class="hero-name">Joel Brandt</h1>
    <p class="hero-role">Senior Scrum Master &amp;amp; Team Agile Coach</p>
    <a class="btn-solid" href="#">Insert Bio Here</a>
  </div>
  <div class="hero-portrait" role="img" aria-label="Portrait photo of Joel Brandt in a blue plaid suit, set against a blue arch"></div>
</section>

<header class="site-header">
  <div class="brand">Q's and V's</div>
  <nav class="main-nav">
    <a href="#">Who am I</a><a href="#">Agile</a><a href="#">Team</a><a href="#">Program</a><a href="#">Under Construction</a><a href="#">Slide Decks</a>
  </nav>
</header>

<section class="designations">
  <h2 class="section-title-light">Coaching Designations</h2>
  <div class="badge-row">
    <div class="badge" style="left:105px"><span style="background:#1f3a66"></span></div>
    <div class="badge" style="left:320px"><span style="background:#f2a13a"></span></div>
    <div class="badge" style="left:534px"><span style="background:#1a9ad9"></span></div>
    <div class="badge" style="left:749px"><span style="background:#22354f"></span></div>
    <div class="badge" style="left:964px"><span style="background:#f4b53c"></span></div>
  </div>
  <div class="profile-links">
    <a class="profile-link" href="#" style="left:287px;width:219px">Sprint Guild Profile Link</a>
    <a class="profile-link" href="#" style="left:519px;width:162px">Badgely Profile Link</a>
    <a class="profile-link" href="#" style="left:694px;width:219px">LIMBr Alliance Profile Link</a>
  </div>
</section>

<section class="services">
  <h2 class="section-title">What I Do</h2>
  <svg width="0" height="0" style="position:absolute">
    <defs><linearGradient id="iconGrad" x1="0" y1="0" x2="0" y2="1"><stop offset="0" stop-color="#0a86cc"/><stop offset="1" stop-color="#13508f"/></linearGradient></defs>
  </svg>
  <div class="service" style="left:105px">
    <div class="service-card">
      <svg width="116" height="116" viewBox="0 0 116 116" fill="none" stroke="url(#iconGrad)" stroke-width="7" stroke-linecap="round">
        <path d="M30 90 A36 36 0 1 1 88 76"/><path d="M20 96 H108 M98 86 L108 96 L98 106"/>
        <path d="M30 12 L24 22 M30 12 L40 18"/>
        <circle cx="58" cy="50" r="7" fill="url(#iconGrad)" stroke="none"/><path d="M46 72 Q58 56 70 72 Z" fill="url(#iconGrad)" stroke="none"/>
      </svg>
    </div>
    <p class="service-name">Sr. Scrum Master</p>
  </div>
  <div class="service" style="left:372px">
    <div class="service-card">
      <svg width="116" height="116" viewBox="0 0 116 116" fill="url(#iconGrad)">
        <rect x="12" y="6" width="92" height="54" rx="4"/><path d="M50 60 L58 70 L66 60 Z"/>
        <circle cx="58" cy="34" r="12" fill="none" stroke="#fff" stroke-width="4"/>
        <circle cx="58" cy="84" r="6"/><rect x="50" y="92" width="16" height="18" rx="3"/>
        <circle cx="18" cy="84" r="6"/><rect x="10" y="92" width="16" height="18" rx="3"/>
        <circle cx="98" cy="84" r="6"/><rect x="90" y="92" width="16" height="18" rx="3"/>
        <rect x="28" y="100" width="60" height="5"/>
      </svg>
    </div>
    <p class="service-name">Advanced LIMBr<br>Scrum Master</p>
  </div>
  <div class="service" style="left:639px">
    <div class="service-card">
      <svg width="116" height="116" viewBox="0 0 116 116" fill="url(#iconGrad)">
        <circle cx="48" cy="34" r="22"/><path d="M10 104 V86 Q10 64 48 64 Q66 64 74 70 L64 104 Z"/>
        <circle cx="84" cy="86" r="18"/>
        <g stroke="url(#iconGrad)" stroke-width="8"><path d="M84 62 V110 M60 86 H108 M67 69 L101 103 M101 69 L67 103"/></g>
        <circle cx="84" cy="86" r="7" fill="#fff"/>
      </svg>
    </div>
    <p class="service-name">Hybrid Scrum Master/<br>Project Manager</p>
  </div>
  <div class="service" style="left:905px">
    <div class="service-card">
      <svg width="100" height="100" viewBox="0 0 100 100" fill="url(#iconGrad)">
        <path d="M34 22 V14 Q34 10 38 10 H62 Q66 10 66 14 V22 H58 V17 H42 V22 Z"/>
        <rect x="4" y="24" width="92" height="66" rx="6"/>
        <rect x="4" y="50" width="92" height="3" fill="#fff"/><rect x="43" y="45" width="14" height="12" fill="#fff"/>
      </svg>
    </div>
    <p class="service-name">Business</p>
  </div>
</section>

<section class="experience">
  <h2 class="section-title">What Is My Experience</h2>
  <div class="exp-grid">
    <div class="exp-photo" role="img" aria-label="Photo of a business team shaking hands around an office table" style="background:linear-gradient(160deg,#e9e6e2,#b9b3ab)"></div>
    <div class="exp-text">
      <h3>As a Hybrid Scrum Master /<br>Project Manager, I:</h3>
      <p>standup teams,run multiple program level projects simultaneously ,implement custom hybrid development strategies,manage to project triple constraints ,communications lead and business liaison , use multiple coaching styles based on team and project</p>
    </div>
    <div class="exp-photo" role="img" aria-label="Close-up photo of Joel Brandt" style="background:linear-gradient(160deg,#9a8a7c,#5a4638)"></div>
    <div class="exp-text">
      <h3>As a LIMBr Adv Scrum<br>Master, I:</h3>
      <p>stand up teams,run development efforts concurrently leading multiple teams ,run LIMBr ceremonies ,Scrum of Scrums facilitator ,PI Planning team facilitator (multiple teams on ART),Teach and coach to advanced development team strategies</p>
    </div>
    <div class="exp-photo" role="img" aria-label="Photo of two business people shaking hands in a modern office" style="background:linear-gradient(160deg,#7d8fa3,#2c3543)"></div>
    <div class="exp-text">
      <h3>Business Transformation<br>Program Manager</h3>
      <p>lead business transformation efforts at the program level,work with multiple product owners, business analysts, and business stakeholders on requirements,lead the international rollout, onboarding, and support of new transformational CRM tool, Skyledger</p>
    </div>
  </div>
  <a class="btn-solid" href="#">Where does coaching come in to play</a>
</section>

<footer class="site-footer">
  <div class="brand">Q's and V's</div>
  <form class="subscribe">
    <span class="subscribe-field">Enter Email</span>
    <span class="subscribe-btn">SUBMIT</span>
  </form>
  <nav class="footer-nav">
    <a href="#">Who am I</a><span>|</span><a href="#">Agile</a><span>|</span><a href="#">Team</a><span>|</span><a href="#">Program</a><span>|</span><a href="#">Under Construction</a><span>|</span><a href="#">Slide Decks</a>
  </nav>
  <p class="copyright">© 2022 &nbsp;Joel Brandt. | All RightsReserved</p>
</footer>

</body>
</html>
```